Business card design

We need a business card designed completed for a new company. We are a company that works with associations, schools to convert their older text/DVDs into dynamic online and mobile programs. Our initial platform is designed for the legal associations and will enable their lawyers to access their content such as forms, videos, case law and support materials anywhere, anytime. We are also focused on Project Management Associations, Financial Management Associations and IT Associations.

I would like for the business card to have the following information:

Logo

Kent marrowby

President and CEO

kmarrowby@trevantiq.example

Mobile: 555-374-9160

www.trevantiq.example

Tag line: Transforming content into a mobile platform    

I would like it to be double sided, use the colours of the logo, tie into the mobile world

 

Industry/Entity Type

Legal

Logo Text

Trevantiq

```html
<!DOCTYPE html>
<html lang="en">
<head>
<meta charset="utf-8">
<title>Trevantiq business card</title>
<link rel="stylesheet" href="https://fonts.googleapis.com/css2?family=Open+Sans:wght@400;700&display=swap">
<style>
  :root {
    --page-bg: #ecebe8;
    --card-grey: #8f8f8f;
    --card-white: #ffffff;
    --strip-dark: #666666;
    --name-box-grey: #8c8c8c;
    --ink: #333333;
    --ink-soft: #555555;
    --logo-dark: #5e5e5e;
    --logo-light: #ffffff;
  }
  * { margin: 0; padding: 0; box-sizing: border-box; }
  html, body { width: 1200px; height: 800px; overflow: hidden; }
  body {
    position: relative;
    background: var(--page-bg);
    font-family: "Open Sans", Arial, sans-serif;
    color: var(--ink);
  }
  .side-label {
    position: absolute;
    width: 509px;
    text-align: center;
    font-size: 21px;
    color: var(--ink);
  }
  .card {
    position: absolute;
    width: 509px;
    height: 290px;
    border-radius: 20px;
    overflow: hidden;
    box-shadow: 0 4px 10px rgba(0,0,0,0.25);
  }
  .card--grey { background: var(--card-grey); }
  .card--white { background: var(--card-white); }
  .logo-word {
    position: absolute;
    font-weight: 700;
    letter-spacing: -1px;
    line-height: 1;
  }
  .card--grey .logo-word { color: var(--logo-light); }
  .card--white .logo-word { color: var(--logo-dark); }
  .logo-word--corner { left: 35px; top: 30px; font-size: 56px; }
  .logo-word--centre { left: 0; right: 0; top: 95px; text-align: center; font-size: 78px; }
  .name-box {
    position: absolute;
    left: 327px; top: 144px;
    width: 182px; height: 48px;
    display: flex;
  }
  .name-box__label { width: 154px; padding: 5px 0 0 8px; white-space: nowrap; }
  .name-box__strip { width: 28px; background: var(--strip-dark); }
  .card--grey .name-box__label { background: var(--card-white); color: var(--ink-soft); }
  .card--white .name-box__label { background: var(--name-box-grey); color: var(--card-white); }
  .person-name { font-size: 16px; line-height: 20px; }
  .person-role { font-size: 12px; line-height: 16px; }
  .contact-list {
    position: absolute;
    right: 14px; top: 211px;
    list-style: none;
    font-size: 12px;
    color: var(--ink);
    white-space: nowrap;
  }
  .contact-list li { display: flex; align-items: center; height: 20.5px; }
  .contact-list svg { width: 10px; height: 10px; margin-right: 6px; fill: var(--ink-soft); flex: none; }
  .tagline {
    position: absolute;
    left: 35px; top: 230px;
    font-size: 15px;
    line-height: 20px;
    color: var(--ink);
  }
  .web-line {
    position: absolute;
    left: 0; right: 0; top: 252px;
    text-align: center;
    font-size: 16px;
    letter-spacing: 3px;
    color: var(--ink);
  }
</style>
</head>
<body>

<svg width="0" height="0" style="position:absolute" aria-hidden="true">
  <symbol id="icon-phone" viewBox="0 0 10 10"><rect x="2.5" y="0" width="5" height="10" rx="1"/><rect x="3.5" y="1.5" width="3" height="5" fill="#fff"/></symbol>
  <symbol id="icon-mail" viewBox="0 0 10 10"><rect x="0" y="2" width="10" height="7"/><path d="M0 2 L5 6 L10 2" stroke="#fff" fill="none" stroke-width="1"/></symbol>
  <symbol id="icon-web" viewBox="0 0 10 10"><circle cx="5" cy="5" r="5"/><path d="M0 5 H10 M5 0 V10" stroke="#fff" stroke-width="0.7"/><ellipse cx="5" cy="5" rx="2.2" ry="5" fill="none" stroke="#fff" stroke-width="0.7"/></symbol>
</svg>

<div class="side-label" style="left:63px; top:48px;">Front</div>
<div class="side-label" style="left:628px; top:48px;">Back - 1</div>
<div class="side-label" style="left:63px; top:408px;">Back - 2</div>
<div class="side-label" style="left:628px; top:408px;">Back - 3</div>

<section class="card card--grey" style="left:63px; top:90px;">
  <div class="logo-word logo-word--corner">Trevantiq</div>
  <div class="name-box">
    <div class="name-box__label">
      <div class="person-name">Kent marrowby</div>
      <div class="person-role">President and CEO</div>
    </div>
    <div class="name-box__strip"></div>
  </div>
  <ul class="contact-list">
    <li><svg><use href="#icon-phone"/></svg>555-374-9160</li>
    <li><svg><use href="#icon-mail"/></svg>kmarrowby@trevantiq.example</li>
    <li><svg><use href="#icon-web"/></svg>www.trevantiq.example</li>
  </ul>
  <p class="tagline">Transforming content<br>into a mobile platform</p>
</section>

<section class="card card--white" style="left:628px; top:90px;">
  <div class="logo-word logo-word--corner">Trevantiq</div>
  <div class="name-box">
    <div class="name-box__label">
      <div class="person-name">Kent marrowby</div>
      <div class="person-role">President and CEO</div>
    </div>
    <div class="name-box__strip"></div>
  </div>
  <ul class="contact-list">
    <li><svg><use href="#icon-phone"/></svg>555-374-9160</li>
    <li><svg><use href="#icon-mail"/></svg>kmarrowby@trevantiq.example</li>
    <li><svg><use href="#icon-web"/></svg>www.trevantiq.example</li>
  </ul>
  <p class="tagline">Transforming content<br>into a mobile platform</p>
</section>

<section class="card card--grey" style="left:63px; top:450px;">
  <div class="logo-word logo-word--centre">Trevantiq</div>
  <div class="web-line">www.trevantiq.example</div>
</section>

<section class="card card--white" style="left:628px; top:450px;">
  <div class="logo-word logo-word--centre">Trevantiq</div>
  <div class="web-line">www.trevantiq.example</div>
</section>

</body>
</html>
```